Dynamic Business Card for Sports Supplements Company

Hi! I'm looking for an awesome business card to match my existing sports supplement company. I have uploaded my current company logo and screenshot of the front page of my website.

I would like to have something dynamic and interesting and utilize the colors in the website - the reds and purples

The business card should be double sided and focus on a unique eye-catching design on the back and include all the relevant company info.

Most importantly, it should say somewhere: "Sign up on our website for a coupon code."

Target Market(s)

Mostly for women gym goers but it shouldn't be too feminine. It should be in keeping with the website design. It should flow and clearly be connected to it

Industry/Entity Type

Business

Contact Information for Business Card

Lorraine K. Vestal
CEO
LVestal@Quorvanexco.com
www.quorvanexco.com
555.417.3820
P.O. Box 47315
Ashvale, Ohio 00000

Sign up on our website for a coupon code

Font styles to use
Serif
Sans Serif
Other font styles liked:
• Novecento font family and "Quorvanex" is in AR Destine font

Requirements
Must have
• One side should be a bold Quorvanex logo design. Even just the symbol itself may be o.k. (see attached file)

```html
<!DOCTYPE html>
<html lang="en">
<head>
<meta charset="utf-8">
<title>Quorvanex Business Card</title>
<link href="https://fonts.googleapis.com/css2?family=Open+Sans:ital,wght@0,400;0,600;0,700;1,400&display=swap" rel="stylesheet">
<style>
  :root {
    --purple: #5f457f;
    --purple-deep: #4e386b;
    --red: #e4222a;
    --white: #ffffff;
    --stage: #666d70;
  }
  * { margin: 0; padding: 0; box-sizing: border-box; }
  html, body { width: 1200px; height: 900px; overflow: hidden; }
  body {
    background: var(--stage);
    font-family: "Open Sans", Arial, sans-serif;
    position: relative;
  }
  .card {
    position: absolute;
    left: 250px;
    width: 700px;
    height: 400px;
    overflow: hidden;
    box-shadow: 0 10px 24px rgba(0,0,0,0.35);
  }
  .card-front { top: 40px; background: var(--white); }
  .card-back { top: 460px; background: var(--purple); }

  .front-shapes { position: absolute; inset: 0; }

  .brand {
    position: absolute;
    left: 60px;
    top: 50px;
    display: flex;
    align-items: center;
    gap: 14px;
  }
  .brand-dot {
    width: 38px; height: 38px;
    border-radius: 50%;
    background: var(--red);
  }
  .brand-name {
    font-weight: 700;
    font-size: 34px;
    letter-spacing: 1px;
    color: var(--purple);
    text-transform: uppercase;
  }

  .contact-list {
    position: absolute;
    left: 60px;
    top: 132px;
    list-style: none;
  }
  .contact-item {
    display: flex;
    align-items: center;
    gap: 10px;
    font-size: 15px;
    color: var(--purple);
    line-height: 24px;
  }
  .contact-icon { width: 14px; height: 14px; flex: none; }

  .coupon-tag {
    position: absolute;
    left: 60px;
    top: 218px;
    background: var(--purple);
    color: var(--white);
    font-size: 14px;
    font-style: italic;
    padding: 3px 10px;
  }

  .person {
    position: absolute;
    right: 60px;
    top: 148px;
    text-align: left;
  }
  .person-name { color: var(--red); font-size: 25px; font-weight: 400; line-height: 32px; }
  .person-title { color: var(--purple); font-size: 13px; font-weight: 600; }

  .address {
    position: absolute;
    right: 60px;
    bottom: 40px;
    color: var(--white);
    font-size: 16px;
    line-height: 22px;
    text-align: right;
  }

  .back-mark {
    position: absolute;
    inset: 0;
    display: flex;
    align-items: center;
    justify-content: center;
    gap: 18px;
  }
  .back-ring {
    width: 70px; height: 70px;
    border-radius: 50%;
    border: 5px solid var(--white);
  }
  .back-name {
    font-weight: 700;
    font-size: 54px;
    letter-spacing: 2px;
    color: var(--white);
    text-transform: uppercase;
  }
</style>
</head>
<body>

<section class="card card-front" aria-label="Card front">
  <svg class="front-shapes" width="700" height="400" viewBox="0 0 700 400" aria-hidden="true">
    <polygon points="0,322 605,250 700,160 700,400 0,400" fill="var(--purple)"/>
    <polyline points="0,322 605,250 700,160" fill="none" stroke="var(--red)" stroke-width="5"/>
  </svg>

  <div class="brand">
    <span class="brand-dot"></span>
    <span class="brand-name">Quorvanex</span>
  </div>

  <ul class="contact-list">
    <li class="contact-item">
      <svg class="contact-icon" viewBox="0 0 16 16"><path d="M3 1l3 3-2 2c1 2 3 4 5 5l2-2 3 3-2 3C6 14 2 10 1 3z" fill="var(--red)"/></svg>
      555.417.3820
    </li>
    <li class="contact-item">
      <svg class="contact-icon" viewBox="0 0 16 16"><rect x="1" y="3" width="14" height="10" fill="var(--red)"/><polyline points="1,3 8,9 15,3" fill="none" stroke="#fff" stroke-width="1.4"/></svg>
      LVestal@Quorvanexco.com
    </li>
    <li class="contact-item">
      <svg class="contact-icon" viewBox="0 0 16 16"><circle cx="8" cy="8" r="7" fill="var(--red)"/><path d="M1 8h14M8 1c-3 3-3 11 0 14M8 1c3 3 3 11 0 14" fill="none" stroke="#fff" stroke-width="1"/></svg>
      www.quorvanexco.com
    </li>
  </ul>

  <p class="coupon-tag">Sign up on our website for a coupon code</p>

  <div class="person">
    <p class="person-name">Lorraine K. Vestal</p>
    <p class="person-title">CEO</p>
  </div>

  <p class="address">P.O. Box 47315<br>Ashvale, Ohio 00000</p>
</section>

<section class="card card-back" aria-label="Card back">
  <div class="back-mark">
    <span class="back-ring"></span>
    <span class="back-name">Quorvanex</span>
  </div>
</section>

</body>
</html>
```